Online tuition webpage design needed

Hi,
We are starting up an online tuition website for non- English speakers wishing to take an TOVAR test.

The webpage must include a place for people to enroll online in the course.
The home page must have:
• room for a logo (coming shortly, blue in colour)
• different packages of online tuition and paywick
• tool bar showing different pages
• perhaps a video, small pictures

This is my site currently:-

www.lexavotutoring.com

as you can see, I am not very sure how to create a website … The large logo is what I would like to use, but I project has not been finalized yet. Please note, I don’t like the logo being that large!

Sites that are similar to what I am doing and like the design of are:

http://www.brindacourse.com.au/fees

https://www.quorvel9x.net/index.php

http://www.lessonmasterpercival.co.uk/index.html

http://www.tamrunexamhub.com/

One thing I need is a place for student s to enroll, and if possible, I would like to use learnix to create exercises for students.
Currently, my site is using sitecraft. My preference is to use learnix for online activities. I am not sure if I can use both.
Thanks in advance

Target Market(s)

people wising to take an TOVAR test (English proficiency test)

Industry/Entity Type

Online

Colors
3276b5
0292cd

Requirements
Must have
• a place for enrollment and admin login for students
learnix
video
voxly, friendbook, chirpnet logos
Nice to have
• a booking calender
Should not have
• too much clutter. must be clean and professional looking

```html
<!DOCTYPE html>
<html lang="en">
<head>
<meta charset="utf-8">
<title>TOVAR Online Tuition</title>
<link rel="stylesheet" href="https://fonts.googleapis.com/css2?family=Source+Sans+3:wght@400;600;700&family=Quicksand:wght@700&display=swap">
<style>
:root{
  --blue:#3276b5;
  --sky:#0292cd;
  --nav-top:#2fa7df;
  --nav-bot:#1b8acb;
  --band:#2a6cae;
  --page:#f5eced;
  --white:#ffffff;
  --ink:#1e1e1e;
  --dark:#262626;
  --green:#7cb82f;
  --gold:#f5b800;
  --line:#c9c9c9;
}
*{margin:0;padding:0;box-sizing:border-box}
html,body{width:934px;height:1200px;overflow:hidden}
body{position:relative;background:var(--page);font-family:"Source Sans 3",Arial,sans-serif;color:var(--ink)}
.abs{position:absolute}
.header{left:0;top:0;width:934px;height:95px;background:var(--white)}
.brand{left:96px;top:24px;display:flex;align-items:center;gap:8px}
.brand-mark{width:30px;height:30px;border-radius:50%;background:var(--blue)}
.brand-name{font-size:40px;font-weight:400;color:var(--blue);letter-spacing:1px}
.search{left:645px;top:21px;width:211px;height:27px;border:1px solid var(--line);border-radius:6px;background:#f4f4f4;font-size:11px;color:var(--sky);padding:7px 10px}
.search svg{position:absolute;right:8px;top:5px}
.login{left:717px;top:58px;width:140px;height:29px;background:var(--green);color:var(--white);font-weight:700;font-size:11px;display:flex;align-items:center;justify-content:center}
.nav{left:0;top:95px;width:934px;height:39px;background:linear-gradient(var(--nav-top),var(--nav-bot));display:flex;align-items:center;padding-left:89px;gap:17px}
.nav a{color:var(--white);font-size:11px;text-decoration:none}
.band{left:0;top:134px;width:934px;height:191px;background:linear-gradient(#2d75b6,var(--band))}
.slider{left:76px;top:162px;width:780px;height:262px;background:var(--white);box-shadow:0 8px 8px -6px rgba(0,0,0,.5)}
.slide{left:12px;top:11px;width:755px;height:239px;background:var(--dark)}
.slide-photo{left:80px;top:30px;width:290px;height:209px;background:radial-gradient(ellipse at 55% 40%,#5a4438,#2b2b2b 70%)}
.slide-title{left:379px;top:18px;font-family:"Quicksand",sans-serif;font-weight:700;font-size:38px;color:var(--gold)}
.slide-list{left:384px;top:83px;list-style:none;color:var(--white);font-size:12px;line-height:24.5px}
.slide-cta{left:382px;top:189px;width:140px;height:33px;background:var(--green);color:var(--white);font-size:18px;display:flex;align-items:center;justify-content:center}
.arrow{width:32px;height:32px;border-radius:50%;background:var(--white);box-shadow:0 1px 3px rgba(0,0,0,.4);display:flex;align-items:center;justify-content:center;top:284px}
.welcome{left:0;top:440px;width:934px;text-align:center;font-size:25px;font-weight:400}
.welcome strong{font-weight:400;color:var(--blue);font-size:38px}
.tagline{left:0;top:482px;width:934px;text-align:center;font-size:23px}
.plan{width:260px;text-align:center}
.plan h2{font-weight:400;color:var(--blue);font-size:24px;height:47px}
.plan-icon{width:100px;height:122px;margin:0 auto;background:#3a3a3a;border-radius:6px}
.plan p{font-size:10.5px;line-height:14px;margin-top:20px;white-space:nowrap}
.btn{display:flex;align-items:center;justify-content:center;width:119px;height:29px;margin:15px auto 0;background:var(--blue);color:var(--white);font-size:11px;border-radius:2px}
.pay{width:75px;height:17px;margin:9px auto 0;border-radius:3px;background:var(--white);border:1px solid var(--line);font-size:10px;font-weight:600;color:var(--ink);display:flex;align-items:center;justify-content:center}
.cards{display:flex;gap:4px;justify-content:center;margin-top:9px}
.cards span{width:30px;height:19px;border-radius:2px;border:1px solid #bbb;background:#e9edf3}
.divider{left:0;top:878px;width:934px;height:255px;background:var(--white);border-top:2px solid #d8d2d3}
.col-title{font-weight:400;color:var(--blue);font-size:23px;text-align:center;line-height:29px}
.voxly{left:160px;top:1018px;display:flex;align-items:center;gap:8px}
.voxly-dot{width:26px;height:26px;border-radius:50%;background:var(--sky)}
.voxly-name{font-size:30px;color:var(--sky);font-weight:600}
.addme{left:152px;top:1086px;width:118px;height:30px;background:var(--blue);color:var(--white);font-weight:700;font-size:14px;display:flex;align-items:center;justify-content:center}
.calendar{left:363px;top:942px;width:214px;height:173px;background:#2c2c2c;border-radius:3px;padding:4px;box-shadow:0 0 3px rgba(0,0,0,.6)}
.cal-head{height:20px;color:var(--white);font-size:9px;font-weight:600;display:flex;align-items:center;justify-content:space-between;padding:0 3px}
.cal-head i{width:11px;height:11px;border-radius:50%;background:#555;display:block}
.calendar table{width:100%;border-collapse:collapse;font-size:8px;text-align:center;background:#f2f2f2}
.calendar th{font-weight:400;font-style:italic;color:#555;height:18px;background:#dcdcdc}
.calendar td{height:20px;border:1px solid #c8c8c8}
.calendar td.mute{color:#aaa}
.calendar td.today{background:#4a9ee0;color:var(--white)}
.video{left:620px;top:942px;width:229px;height:171px;background:#111}
.video-bar{left:0;top:0;width:229px;height:18px;color:var(--white);font-size:8px;padding:4px 5px}
.video-frame{left:12px;top:20px;width:205px;height:130px;background:linear-gradient(#f4f4f4,#d9d9d9)}
.video-ctrl{left:0;top:152px;width:229px;height:19px;color:#ccc;font-size:7px;display:flex;align-items:center;gap:8px;padding:0 8px}
.footer-links{left:76px;top:1153px;font-size:9px}
.footer-links span{margin:0 4px}
.copy{left:76px;top:1173px;font-size:9px}
.social{left:690px;top:1157px;width:166px;display:flex;justify-content:flex-end;gap:7px;font-size:9px;font-weight:600;color:var(--ink)}
</style>
</head>
<body>
<header class="abs header">
  <div class="abs brand"><span class="brand-mark"></span><span class="brand-name">TOVAR</span></div>
  <div class="abs search">SEARCH
    <svg width="14" height="14" viewBox="0 0 14 14"><circle cx="5.5" cy="5.5" r="4" fill="none" stroke="#0292cd" stroke-width="2"/><line x1="8.5" y1="8.5" x2="13" y2="13" stroke="#0292cd" stroke-width="2.4"/></svg>
  </div>
  <div class="abs login">STUDENT LOGIN</div>
</header>
<nav class="abs nav">
  <a>Home</a><a>Courses</a><a>Fees</a><a>Testimonials</a><a>Agents</a><a>FAQ</a><a>About Us</a><a style="margin-left:6px">Contact Us</a>
</nav>
<div class="abs band"></div>
<section class="abs slider">
  <div class="abs slide">
    <div class="abs slide-photo" role="img" aria-label="Student with headset working on a laptop"></div>
    <div class="abs slide-title">Top Courses</div>
    <ul class="abs slide-list"><li>Business English</li><li>Conversation</li><li>Custom-made program</li><li>Job interview preparation</li></ul>
    <div class="abs slide-cta">REGISTER NOW</div>
  </div>
</section>
<div class="abs arrow" style="left:66px"><svg width="12" height="14"><polyline points="9,2 3,7 9,12" fill="none" stroke="#111" stroke-width="3"/></svg></div>
<div class="abs arrow" style="left:836px"><svg width="12" height="14"><polyline points="3,2 9,7 3,12" fill="none" stroke="#111" stroke-width="3"/></svg></div>

<h1 class="abs welcome">Welcome To <strong>TOVAR</strong> Online Tuition</h1>
<p class="abs tagline">We put you first. We listen to you and help you find what you need.</p>

<section class="abs plan" style="left:78px;top:538px">
  <h2>The Standard Plan</h2>
  <div class="plan-icon" role="img" aria-label="Teacher with pointer pictogram"></div>
  <p>Lorem ipsum dolor sit amet, consectetur<br>adipisicing elit, sed do eiusmod tempor incididunt ut<br>labore et dolore magna aliqua.</p>
  <div class="btn">Register Now</div>
  <div class="pay">Pay Now</div>
  <div class="cards"><span></span><span></span><span></span><span></span></div>
</section>
<section class="abs plan" style="left:339px;top:538px">
  <h2>The Gold Plan</h2>
  <div class="plan-icon" role="img" aria-label="Payment card and coins pictogram"></div>
  <p>Lorem ipsum dolor sit amet, consectetur<br>adipisicing elit, sed do eiusmod tempor incididunt ut<br>labore et dolore magna aliqua.</p>
  <div class="btn">Register Now</div>
  <div class="pay">Pay Now</div>
  <div class="cards"><span></span><span></span><span></span><span></span></div>
</section>
<section class="abs plan" style="left:602px;top:538px">
  <h2>The Diamond Plan</h2>
  <div class="plan-icon" role="img" aria-label="Book with download arrow pictogram"></div>
  <p>Lorem ipsum dolor sit amet, consectetur<br>adipisicing elit, sed do eiusmod tempor incididunt ut<br>labore et dolore magna aliqua.</p>
  <div class="btn">Register Now</div>
  <div class="pay">Pay Now</div>
  <div class="cards"><span></span><span></span><span></span><span></span></div>
</section>

<div class="abs divider"></div>
<h3 class="abs col-title" style="left:66px;top:901px;width:280px">High quality voxly<br>English lessons with a<br>British native speaker</h3>
<div class="abs voxly"><span class="voxly-dot"></span><span class="voxly-name">voxly</span></div>
<div class="abs addme">ADD ME</div>

<h3 class="abs col-title" style="left:363px;top:901px;width:214px">Book Class</h3>
<div class="abs calendar">
  <div class="cal-head"><i></i>Lipiec, 2011<i></i></div>
  <table>
    <tr><th>Sob</th><th>Pon</th><th>Wto</th><th>Śro</th><th>Czw</th><th>Pią</th><th>Nied</th></tr>
    <tr><td class="mute">27</td><td class="mute">28</td><td class="mute">29</td><td class="mute">30</td><td>1</td><td>2</td><td>3</td></tr>
    <tr><td>4</td><td>5</td><td class="today">6</td><td>7</td><td>8</td><td>9</td><td>10</td></tr>
    <tr><td>11</td><td>12</td><td>13</td><td>14</td><td>15</td><td>16</td><td>17</td></tr>
    <tr><td>18</td><td>19</td><td>20</td><td>21</td><td>22</td><td>23</td><td>24</td></tr>
    <tr><td>25</td><td>26</td><td>27</td><td>28</td><td>29</td><td>30</td><td>31</td></tr>
    <tr><td class="mute">1</td><td class="mute">2</td><td class="mute">3</td><td class="mute">4</td><td class="mute">5</td><td class="mute">6</td><td class="mute">7</td></tr>
  </table>
</div>

<h3 class="abs col-title" style="left:620px;top:897px;width:229px">Our Video</h3>
<div class="abs video">
  <div class="abs video-bar">TOVAR Promo Video www.quorvel9x.net</div>
  <div class="abs video-frame" role="img" aria-label="Presenter introducing the tuition service"></div>
  <svg class="abs" style="left:101px;top:71px" width="28" height="28"><circle cx="14" cy="14" r="14" fill="rgba(0,0,0,.7)"/><polygon points="11,8 20,14 11,20" fill="#fff"/></svg>
  <div class="abs video-ctrl"><svg width="8" height="8"><polygon points="0,0 8,4 0,8" fill="#ccc"/></svg>0:00 / 1:38</div>
</div>

<footer>
  <div class="abs footer-links">Home<span>|</span>Privacy Policy<span>|</span>Terms &amp; Conditions<span>|</span>Testimonials<span>|</span>Sitemap</div>
  <div class="abs copy">Copyrights 2014 All rights reserved</div>
  <div class="abs social"><span>chirpnet</span><span>linkvane</span><span>gplexo</span><span>friendbook</span></div>
</footer>
</body>
</html>
```